Playful Website Design Needed Pet Sitting and Dog Walking Business

Need a simple one page Web Design Built on WordPress.
Sections:

About Us
Services Provided
Costs
Contact Us
Intake Form (Questionnaire that goes to email)
See us in Action

Industry/Entity Type

Pet Sitting and Dog Walking

Number of Pages Required

1 page

Font styles to use
Other font styles liked:
• See the Business Card Font and use that.

Colors
EE7325
F08F49
F5BC92
FAE3D3
FDF4ED

Requirements
Must have
• See attached Logo Design, with Font's and Colors Use these as theme guide

```html
<!DOCTYPE html>
<html lang="en">
<head>
<meta charset="utf-8">
<title>Paw Pals Sitting</title>
<link rel="stylesheet" href="https://fonts.googleapis.com/css2?family=Fredoka:wght@500;600&family=Roboto+Condensed:wght@400;700&display=swap">
<style>
:root{
  --red:#ff4b06;
  --yellow:#ffe60a;
  --green:#6dbe35;
  --orange:#ee7325;
  --ink:#111;
  --body:#333;
  --white:#fff;
}
*{box-sizing:border-box;margin:0;padding:0}
html,body{width:1200px;height:4601px;overflow:hidden}
body{position:relative;background:var(--white);font-family:"Roboto Condensed",Arial,sans-serif;color:var(--body)}
.abs{position:absolute}
.display{font-family:"Fredoka",Arial,sans-serif;font-weight:600;color:var(--ink)}
.logo{display:flex;align-items:center;gap:10px;font-family:"Fredoka",Arial,sans-serif;font-weight:600;color:var(--orange)}
.logo-dot{width:26px;height:26px;border-radius:50%;background:var(--yellow);flex:none}
.nav{display:flex;gap:0;font-weight:700;font-size:14px;color:var(--ink);text-transform:uppercase}
.nav a{color:inherit;text-decoration:none;position:absolute}
.nav .active{color:var(--green)}
.btn{position:absolute;display:flex;align-items:center;justify-content:center;background:var(--green);color:var(--white);font-weight:700;font-size:18px;text-transform:uppercase;border-radius:40px 0 40px 0;text-decoration:none}
.para{position:absolute;font-size:15px;line-height:24.6px;text-align:justify}
/* hero */
.hero-photo{left:0;top:0;width:1200px;height:780px;background:linear-gradient(180deg,#cfd8c8 0%,#7ea85c 35%,#5b7d43 55%,#9a9a94 75%,#b9b7b0 100%)}
.hero-fade{left:0;top:0;width:1200px;height:300px;background:radial-gradient(ellipse 520px 260px at 150px 40px,rgba(255,255,255,.95),rgba(255,255,255,0))}
.hero-circle{left:149px;top:161px;width:410px;height:410px;border-radius:50%;background:rgba(255,255,255,.72);border:6px solid rgba(200,230,170,.8)}
.hero-title{left:150px;top:262px;width:410px;text-align:center;font-size:46px;line-height:42px}
.hero-title .hl{color:var(--orange)}
.dot{width:9px;height:9px;border-radius:50%;background:var(--white)}
.dot.on{width:13px;height:13px;border:2px solid var(--green)}
/* services */
.svc-ring{border-radius:50%;border:14px solid var(--orange)}
.svc-photo{border-radius:50%}
.svc-title{font-family:"Roboto Condensed",Arial,sans-serif;font-weight:700;font-size:36px;color:var(--ink)}
.field{position:absolute;border:2px solid #444;background:var(--white);font-size:16px;color:#333;padding:22px 0 0 32px}
.contact-icon{width:68px;height:68px;border-radius:50%;background:var(--white);display:flex;align-items:center;justify-content:center}
.contact-text{width:240px;text-align:center;color:var(--white);font-size:15px;line-height:25px}
</style>
</head>
<body>

<!-- Hero -->
<div class="abs hero-photo" role="img" aria-label="Photo of a smiling woman walking several dogs on leashes along a leafy park path"></div>
<div class="abs hero-fade"></div>

<header>
  <div class="abs logo" style="left:143px;top:40px;font-size:30px"><span class="logo-dot"></span>Paw Pals Sitting</div>
  <nav class="abs nav" style="left:0;top:60px;width:1200px;height:20px">
    <a class="active" style="left:718px">About Us</a>
    <a style="left:811px">Services</a>
    <a style="left:904px">Costs</a>
    <a style="left:975px">Contact Us</a>
  </nav>
</header>

<div class="abs hero-circle"></div>
<h1 class="abs display hero-title">We need, Walk<br>and <span class="hl">Play with</span><br><span class="hl">your</span> Pet, Each<br>visit!</h1>
<a class="btn" style="left:271px;top:461px;width:165px;height:43px;font-size:15px">Contact Us</a>
<div class="abs dot" style="left:987px;top:614px"></div>
<div class="abs dot" style="left:1010px;top:614px"></div>
<div class="abs dot on" style="left:1033px;top:612px"></div>

<!-- About -->
<svg class="abs" style="left:0;top:600px" width="1200" height="640" viewBox="0 600 1200 640" aria-hidden="true">
  <ellipse cx="600" cy="920" rx="780" ry="297" fill="var(--red)"/>
  <ellipse cx="600" cy="920" rx="720" ry="215" fill="var(--yellow)"/>
</svg>
<h2 class="abs display" style="left:146px;top:842px;font-size:58px">About Us</h2>
<p class="para" style="left:497px;top:854px;width:557px;color:#333">Lorem ipsum dolor sit amet, consectetur adipiscing elit, sed do eiusmod tempor incididunt ut labore et dolore magna aliqua. Quis ipsum suspendisse ultrices gravida. Risus commodo viverra maecenas accumsan lacus vel facilisis. Lorem ipsum dolor sit amet, consectetur adipiscing elit, sed do eiusmod tempor incididunt ut labore et dolore magna aliquis ipsum suspendisse ultrices gravsus commodo</p>
<a class="btn" style="left:500px;top:1009px;width:197px;height:54px">Get Started</a>

<!-- Services -->
<h2 class="abs display" style="left:0;top:1315px;width:1200px;text-align:center;font-size:60px">Services Provided</h2>

<div class="abs svc-ring" style="left:169px;top:1477px;width:340px;height:340px"></div>
<div class="abs svc-photo" style="left:211px;top:1512px;width:270px;height:270px;background:radial-gradient(circle at 45% 45%,#a8b070,#4f6a2e 70%,#3a4d24)" role="img" aria-label="Photo of a person crouching on grass with two dogs"></div>
<h3 class="abs svc-title" style="left:568px;top:1492px">Pet Sitting</h3>
<p class="para" style="left:568px;top:1567px;width:462px">Lorem ipsum dolor sit amet, consectetur adipiscing elit, sed do eiusmod tempor incididunt ut labore et dolore magna aliqua. Quis ipsum suspendisse ultrices gravida. Risus commodo viverra maecenas accumsan lacus vel facilisis. Lorem ipsum dolor sit amet, consectetur adipiscing elit, sed do eiusmod tempor incididunt ut labore et dolore magna aliquis ipsum suspendisse ultrices gravsus commodo</p>
<a class="btn" style="left:568px;top:1745px;width:200px;height:54px">Get Started</a>

<h3 class="abs svc-title" style="left:168px;top:1947px">Dog Walking</h3>
<p class="para" style="left:168px;top:2021px;width:464px">Lorem ipsum dolor sit amet, consectetur adipiscing elit, sed do eiusmod tempor incididunt ut labore et dolore magna aliqua. Quis ipsum suspendisse ultrices gravida. Risus commodo viverra maecenas accumsan lacus vel facilisis. Lorem ipsum dolor sit amet, consectetur adipiscing elit, sed do eiusmod tempor incididunt ut labore et dolore magna aliquis ipsum suspendisse ultrices gravsus commodo</p>
<a class="btn" style="left:170px;top:2200px;width:200px;height:54px">Get Started</a>
<div class="abs svc-ring" style="left:684px;top:1941px;width:340px;height:340px"></div>
<div class="abs svc-photo" style="left:719px;top:1976px;width:270px;height:270px;background:radial-gradient(circle at 50% 40%,#c9d6b8,#6f8f4d 65%,#3f5a2c)" role="img" aria-label="Photo of a group of people walking many dogs on a tree-lined path"></div>

<!-- Costs -->
<div class="abs" style="left:54px;top:2407px;width:1093px;height:590px;background:var(--red);border-radius:330px 0 330px 0"></div>
<div class="abs" style="left:136px;top:2488px;width:928px;height:425px;background:var(--green);border-radius:260px 0 260px 0"></div>
<h2 class="abs display" style="left:0;top:2546px;width:1200px;text-align:center;font-size:60px;color:var(--white)">Costs</h2>
<p class="abs" style="left:262px;top:2642px;width:676px;text-align:center;color:var(--white);font-size:15px;line-height:24.6px">Lorem ipsum dolor sit amet, consectetur adipiscing elit, sed do eiusmod tempor incididunt ut labore et dolore magna aliqua. Quis ipsum suspendisse ultrices gravida. Risus commodo viverra maecenas accumsan lacus vel facilisis. Lorem ipsum dolor sit amet, consectetur adipiscing elit, sed do eiusmod tempor incididunt ut labore et dolore magna aliquis ipsum suspendisse ultrices gravsus commodo</p>
<a class="btn" style="left:504px;top:2786px;width:193px;height:54px;background:var(--yellow);color:var(--red);border:4px solid var(--red)">Read More</a>

<!-- Contact form -->
<h2 class="abs display" style="left:0;top:3104px;width:1200px;text-align:center;font-size:60px">Contact Form</h2>
<form>
  <div class="field" style="left:250px;top:3233px;width:341px;height:64px">Enter Name</div>
  <div class="field" style="left:609px;top:3233px;width:341px;height:64px">Enter Email</div>
  <div class="field" style="left:250px;top:3317px;width:341px;height:64px">Phone</div>
  <div class="field" style="left:609px;top:3317px;width:341px;height:64px">Address</div>
  <div class="field" style="left:250px;top:3402px;width:700px;height:111px">Message</div>
  <a class="btn" style="left:504px;top:3549px;width:193px;height:54px">Submit</a>
</form>

<!-- Contact us -->
<div class="abs" style="left:21px;top:3679px;width:1158px;height:625px;background:var(--yellow);border-radius:360px 0 360px 0"></div>
<div class="abs" style="left:104px;top:3763px;width:993px;height:461px;background:var(--red);border-radius:270px 0 270px 0"></div>
<h2 class="abs display" style="left:0;top:3798px;width:1200px;text-align:center;font-size:60px;color:var(--white)">Contact Us</h2>

<div class="abs contact-icon" style="left:325px;top:3920px">
  <svg width="26" height="32" viewBox="0 0 26 32"><path d="M13 1C6.4 1 1 6.3 1 12.8 1 21.5 13 31 13 31s12-9.5 12-18.2C25 6.3 19.6 1 13 1z" fill="var(--red)"/><circle cx="13" cy="12.5" r="4.5" fill="#fff"/></svg>
</div>
<div class="abs contact-text" style="left:239px;top:4006px">123,Nemo enim ipsam<br>voluptatem quia voluptas</div>

<div class="abs contact-icon" style="left:566px;top:3920px">
  <svg width="26" height="26" viewBox="0 0 24 24"><path d="M6.6 10.8a15.1 15.1 0 0 0 6.6 6.6l2.2-2.2a1 1 0 0 1 1-.25 11.4 11.4 0 0 0 3.6.57 1 1 0 0 1 1 1V20a1 1 0 0 1-1 1A17 17 0 0 1 3 4a1 1 0 0 1 1-1h3.5a1 1 0 0 1 1 1c0 1.25.2 2.45.57 3.57a1 1 0 0 1-.25 1z" fill="var(--red)"/></svg>
</div>
<div class="abs contact-text" style="left:480px;top:4006px;font-weight:700;font-size:18px">Phone<br>+1 888 888 8888</div>

<div class="abs contact-icon" style="left:807px;top:3920px">
  <svg width="24" height="18" viewBox="0 0 24 18"><rect x="0" y="0" width="24" height="18" rx="2" fill="var(--red)"/><path d="M1 2l11 8 11-8" fill="none" stroke="#fff" stroke-width="2"/></svg>
</div>
<div class="abs contact-text" style="left:721px;top:4006px">Email<br>info@pawpalssitting.com</div>

<a class="btn" style="left:504px;top:4115px;width:193px;height:54px">Get Started</a>

<!-- Footer -->
<footer>
  <div class="abs logo" style="left:152px;top:4430px;font-size:38px"><span class="logo-dot" style="width:34px;height:34px"></span>Paw Pals Sitting</div>
  <nav class="abs nav" style="left:0;top:4380px;width:1200px;height:20px;font-size:16px;text-transform:uppercase">
    <a style="left:523px">About Us</a>
    <a style="left:634px">Services</a>
    <a style="left:741px">Costs</a>
    <a style="left:825px">Contact Us</a>
  </nav>
  <p class="abs" style="left:523px;top:4430px;font-size:16px;color:#333">© 2022 Paw Pals Sitting. All rights reserved.Privacy &nbsp;| Terms of Use</p>
  <svg class="abs" style="left:524px;top:4484px" width="38" height="38" viewBox="0 0 38 38" aria-label="Website">
    <g fill="none" stroke="var(--red)" stroke-width="3"><circle cx="19" cy="19" r="16"/><ellipse cx="19" cy="19" rx="7" ry="16"/><path d="M3 19h32M6 11h26M6 27h26"/></g>
  </svg>
  <svg class="abs" style="left:584px;top:4488px" width="42" height="30" viewBox="0 0 42 30" aria-label="Email">
    <rect x="2" y="2" width="38" height="26" rx="2" fill="none" stroke="var(--red)" stroke-width="3.5"/><path d="M3 4l18 14L39 4" fill="none" stroke="var(--red)" stroke-width="3.5"/>
  </svg>
</footer>

</body>
</html>
```